Bold, Modern, Clean "Kestrelwaymassage.com" website

Why we stand out?
We are a male and female mobile massage team. Our names are Paul and Lina. 
Kestrel Way is a Seattle based mobile massage service. Our massage is offered to the community with a goal of facilitating balance within each individual. We specialize in integrated Pain management, and sports/medical massage therapy. Every client's first assessment is attended by our male and female massage therapist team. Depending on the goals identified for an individual determines which therapist will be assigned to provide treatment, if not both.

Our passion...
Here at Kestrel Way, we have a great passion for Postural Resoration and how it is integrated into an individual's Massage treatment. We pride ourselves in being natural facilitators of healing, which takes the ego of the therapist out of the client's healing process. We strive to deliver the best massage possible by including modalities such as Neuromuscular, Myofascial release, spontaneous muscle release, postural restoration, orthopedic, and medical massage.

Our education...

We are both Graduates of Venmora, school of massage therapy. We have continuing education in medical massage, myofacial release, trigger point therapy, postural restoration, anatomy, and spontaneous muscle release. Lina is also a Certified Yoga Instructor, which amplifies her experience with flexibility and strength as it pertains to each individual. Paul's passion is Massage, stretching, and strength training to encourage postural restoration and realignment.

Our rates-

Our rates are $75/ 60 minutes, $95/ 90 minutes, and $120/ 120 minutes.

Education-
Both Lina and I worked as behavioral health professionals that specialized in life skills mentoring for youth who had experienced different types of trauma. This led us both to want to help others in a different environment, where individuals can be empowered to take responsibility over their own healing. To us, massage is a type of manipulation physical therapy, that encourages healing on many levels.

Advice to any massage client-
The most important thing to 'us', as Licenced providers is to get you on to our table to show you our skills. But a good therapist never forgets that it's not about what we do for you, but what we can facilitate for you. Your health and healing has nothing to do with us. It is yours, not ours. Identify what your goals are with any Therapist, and know what the end looks like. Progress should be tangible, such as range of motion, and decreased pain.

Lina and Paul at Kestrel Way are awesome! I recently had open heart surgery, and Lina worked on me to increase my range of motion while helping with the pinched nerve from my arm being in the same position for so long during my surgery. My wife drives a lot for work, and Paul has helped decrease her neck and lower back pain immensely. They are seriously the best therapists I have ever worked with. I would recommend them to anyone who needs anything from stress relief to a medical massage treatment. They are professional, up beat, easy going, and always on time. And, I love that they meet us where ever we like! We did a staycation recently, where they came to our hotel to give us relaxation massages. Although usually they come to our home, where we focus on pain related issues. We will continue to work with them for a long, long time.

Target Market(s)

Mobile massage therapy clients

Industry/Entity Type

Massage Therapy

Coding

Coded - Design and coding required

Number of Pages Required

1 page

Font styles to use
Serif
Sans Serif

Requirements
Must have
• Please add or remove any information that would help the presentation of our website. Our logo is posted below, please include into the website.
• Please include a contact field that includes, kestrelwaymassage@fernmail.net,
• (206) 555-0148
• We have also included our own stock photos, as well as a photo of Paul and Lina. Please include a cropped photo of both massage therapists.

```html
<!DOCTYPE html>
<html lang="en">
<head>
<meta charset="utf-8">
<title>Kestrel Way – Mobile Massage</title>
<link rel="stylesheet" href="https://fonts.googleapis.com/css2?family=Ubuntu:wght@400;500;700&family=Open+Sans:ital,wght@0,400;0,600;0,700;1,400&display=swap">
<style>
:root{
  --navy:#0c3f7a;
  --blue:#1a6bb0;
  --link:#1f78b8;
  --ink:#333333;
  --muted:#555555;
  --panel:rgba(90,90,90,.72);
  --band:#e6e6e6;
  --footer:#333333;
  --footer-box:#444444;
  --footer-text:#f2f2f2;
  --white:#ffffff;
}
*{box-sizing:border-box;margin:0;padding:0}
html,body{width:1200px;height:2359px;overflow:hidden}
body{position:relative;background:var(--white);font-family:"Open Sans",Arial,sans-serif;color:var(--ink)}
.abs{position:absolute}
a{color:inherit;text-decoration:none}

/* hero */
.hero{left:0;top:0;width:1200px;height:580px;background:linear-gradient(100deg,#dfe3df 0%,#f3f3f1 35%,#ececea 60%,#d9d6d2 100%)}
.top-strip{left:0;top:0;width:1200px;height:3px;background:linear-gradient(90deg,var(--blue),#5aa0d6,var(--blue))}
.brand-badge{display:flex;align-items:center;justify-content:center;border-radius:50%;background:var(--navy);border:4px solid var(--white);box-shadow:0 0 0 1px #c9d3de;color:var(--white);font-family:"Ubuntu",Arial,sans-serif;font-weight:700;text-align:center;line-height:1.05}
.header-logo{left:107px;top:42px;width:106px;height:106px;font-size:17px}
.nav{left:530px;top:96px;font-size:12.5px;color:var(--navy)}
.nav a{position:absolute;white-space:nowrap}
.nav .active::before{content:"";position:absolute;left:0;right:0;top:-14px;height:2px;background:var(--navy)}
.social{top:33px;width:34px;height:34px;border-radius:50%;background:var(--blue)}
.phone{left:966px;top:94px;display:flex;align-items:center;gap:8px;font-family:"Ubuntu",Arial,sans-serif;font-weight:700;font-size:15px;color:var(--navy)}
.contact-form{left:110px;top:208px;width:285px;height:298px;background:var(--panel)}
.contact-form h2{position:absolute;left:36px;top:20px;display:flex;align-items:center;gap:12px;color:var(--white);font-family:"Ubuntu",Arial,sans-serif;font-weight:500;font-size:21px}
.field{position:absolute;left:27px;width:230px;height:38px;border:1px solid rgba(255,255,255,.75);color:var(--white);font-size:11px;padding:11px 14px;letter-spacing:.2px}
.send{position:absolute;left:88px;top:234px;width:107px;height:36px;background:var(--blue);color:var(--white);font-family:"Ubuntu",Arial,sans-serif;font-size:16px;display:flex;align-items:center;justify-content:center;box-shadow:inset 0 -2px 0 rgba(0,0,0,.15)}
.center-logo{left:508px;top:488px;width:184px;height:184px;font-size:30px;border-width:6px}

/* intro */
.section-title{left:0;width:1200px;text-align:center;font-family:"Ubuntu",Arial,sans-serif;font-weight:700;color:var(--navy)}
.intro-title{top:696px;font-size:33px}
.intro-text{left:130px;top:748px;width:940px;text-align:center;font-size:12.5px;line-height:22px;color:var(--ink)}
.feature{width:300px;text-align:center}
.feature .photo{width:190px;height:190px;border-radius:50%;margin:0 auto;border:2px solid #e3e3e3}
.feature h3{margin-top:26px;font-family:"Ubuntu",Arial,sans-serif;font-weight:500;font-size:15.5px;color:var(--ink);letter-spacing:.2px}
.feature p{margin:12px auto 0;width:200px;font-size:12px;line-height:20px;color:var(--ink)}
.read-more{display:block;margin-top:7px;font-size:11.5px;color:var(--link)}

/* rates */
.rates{left:0;top:1240px;width:1200px;height:314px;background:linear-gradient(120deg,#f4f1ee 0%,#fbfaf9 35%,#efe9e4 60%,#f7f5f3 100%)}
.rates-title{top:1282px;font-size:30px}
.rate{width:300px;text-align:center}
.rate .ring{width:98px;height:98px;margin:0 auto;border:2px solid var(--navy);border-radius:50%;display:flex;flex-direction:column;align-items:center;justify-content:center;font-family:"Ubuntu",Arial,sans-serif;font-weight:700;font-size:13px;line-height:22px;color:var(--ink)}
.rate .ring span{color:var(--blue)}
.rate h3{margin-top:14px;font-family:"Ubuntu",Arial,sans-serif;font-weight:400;font-size:15.5px;color:var(--ink)}

/* info columns */
.col-title{font-family:"Ubuntu",Arial,sans-serif;font-weight:700;font-size:16.5px;color:var(--navy)}
.therapy-card{left:99px;top:1633px;width:318px;height:215px;background:linear-gradient(110deg,#6e7d54 0%,#8a9866 40%,#5c6b45 100%);color:var(--white);text-align:center}
.therapy-card h4{margin:41px 0 0 60px;font-family:"Ubuntu",Arial,sans-serif;font-weight:500;font-size:16px}
.stars{margin:6px 0 0 60px;display:flex;justify-content:center}
.therapy-card p{margin:6px 0 0 60px;font-size:12px;line-height:19px;padding:0 22px}
.therapy-card .more{display:block;margin:10px 0 0 55px;font-size:11.5px;font-weight:600}
.col-text{font-size:12px;line-height:22px;color:var(--ink)}
.passion-list{list-style:none}
.passion-list li{display:flex;align-items:center;gap:8px;height:25.8px;font-size:12px}
.edu-text{text-align:justify}

/* testimonials */
.testimonials{left:99px;top:1919px;width:1002px;height:176px;background:var(--band);text-align:center}
.small-logo{left:576px;top:1895px;width:48px;height:48px;font-size:7.5px;border-width:3px}
.testimonials h3{margin-top:50px;font-family:"Ubuntu",Arial,sans-serif;font-weight:500;font-size:15.5px;color:var(--ink)}
.testimonials blockquote{margin:14px auto 0;width:820px;font-style:italic;font-size:12px;line-height:22px;color:var(--ink)}
.testimonials cite{display:block;margin-top:8px;font-style:normal;font-family:"Ubuntu",Arial,sans-serif;font-weight:700;font-size:14px;color:var(--navy)}
.arrow{top:1996px}

/* footer */
.footer{left:0;top:2095px;width:1200px;height:264px;background:var(--footer);color:var(--footer-text)}
.footer-logo{left:127px;top:2124px;width:139px;height:139px;font-size:23px}
.foot-title{font-family:"Ubuntu",Arial,sans-serif;font-weight:500;font-size:15px;color:var(--white)}
.foot-list{list-style:none;font-size:12px;color:var(--footer-text)}
.foot-list li{height:21.5px;display:flex;align-items:center;gap:9px}
.foot-list li::before{content:"»";color:#9aa8b6;font-size:11px}
.tweet-box{left:609px;top:2153px;width:228px;height:122px;background:var(--footer-box);color:var(--footer-text);font-size:11.5px;line-height:19px;padding:14px 14px 0 14px}
.tweet-box .summary{position:absolute;right:12px;bottom:12px;text-decoration:underline;font-size:11.5px}
.contact-item{left:892px;display:flex;gap:16px;align-items:flex-start;font-size:12px;line-height:18px;color:var(--footer-text)}
.contact-item svg{flex:none;margin-top:2px}
.foot-rule{left:0;top:2303px;width:1200px;height:1px;background:#474747}
.copyright{left:0;top:2321px;width:1200px;text-align:center;font-size:11.5px;color:#d8d8d8}
</style>
</head>
<body>

<!-- hero -->
<div class="abs hero" role="img" aria-label="Photo of a therapist stretching a client's arm on a massage table in a bright room"></div>
<div class="abs top-strip"></div>
<div class="abs brand-badge header-logo">Kestrel<br>Way</div>

<nav class="abs nav">
  <a class="active" style="left:13px">Home</a>
  <a style="left:75px">About us</a>
  <a style="left:151px">Services</a>
  <a style="left:225px">Offer</a>
  <a style="left:282px">Blog</a>
  <a style="left:334px">Contacts</a>
</nav>

<div class="abs social" style="left:947px"></div>
<div class="abs social" style="left:987px"></div>
<div class="abs social" style="left:1024px"></div>
<div class="abs social" style="left:1064px"></div>

<div class="abs phone">
  <svg width="24" height="24" viewBox="0 0 24 24" aria-hidden="true"><circle cx="12" cy="12" r="11" fill="none" stroke="#0c3f7a" stroke-width="1.3"/><path d="M9 6.5l1.6 2.6-1.2 1.3c.7 1.6 1.7 2.6 3.2 3.3l1.3-1.2 2.6 1.6-.7 2c-4.5.3-8.3-3.6-8-8z" fill="#0c3f7a"/></svg>
  (206) 555-0148
</div>

<form class="abs contact-form">
  <h2>
    <svg width="26" height="24" viewBox="0 0 26 24" aria-hidden="true"><circle cx="9" cy="5" r="4" fill="#fff"/><path d="M2 22c0-6 3-10 7-10s6 3 7 6h8v4z" fill="#fff"/></svg>
    CONTACT FORM
  </h2>
  <div class="field" style="top:70px">NAME</div>
  <div class="field" style="top:122px">PHONE NUMBER</div>
  <div class="field" style="top:174px">EMAIL ADDRESS</div>
  <div class="send">SEND</div>
</form>

<div class="abs brand-badge center-logo">Kestrel<br>Way</div>

<!-- intro -->
<h1 class="abs section-title intro-title">Why we stand out?</h1>
<p class="abs intro-text">We are a male and female mobile massage team. Our names are Paul and Lina. Kestrel Way is a Seattle based mobile massage service. Our massage is offered to the community with a goal of facilitating balance within each individual. We specialize in integrated Pain management, and sports/medical massage therapy. Every client's first assessment is attended by our male and female massage therapist team. Depending on the goals identified for an individual determines which therapist will be assigned to provide treatment, if not both.</p>

<div class="abs feature" style="left:259px;top:859px">
  <div class="photo" role="img" aria-label="Photo of a relaxed client receiving a shoulder massage" style="background:radial-gradient(circle at 40% 45%,#f3d7c3,#d9a98a 70%,#efe3da)"></div>
  <h3>PAIN MANAGEMENT</h3>
  <p>We are a male and female mobile massage team. Our names are Paul and Lina.balance within ...</p>
  <a class="read-more">READ MORE &gt;&gt;</a>
</div>
<div class="abs feature" style="left:639px;top:859px">
  <div class="photo" role="img" aria-label="Photo of a therapist working on a client's leg and knee" style="background:radial-gradient(circle at 50% 45%,#e9d6c6,#b7c3cf 65%,#48637a)"></div>
  <h3>SPORTS/MEDICAL MASSAGE THERAPY.</h3>
  <p>We are a male and female mobile massage team. Our names are Paul and Lina.balance within ...</p>
  <a class="read-more">READ MORE &gt;&gt;</a>
</div>

<!-- rates -->
<div class="abs rates" role="img" aria-label="Faint background photo of hands massaging a back"></div>
<h2 class="abs section-title rates-title">Our Rates</h2>
<div class="abs rate" style="left:114px;top:1354px">
  <div class="ring">$ 75<span>60 Minutes</span></div>
  <h3>NEUROMUSCULAR</h3>
</div>
<div class="abs rate" style="left:448px;top:1354px">
  <div class="ring">$ 95<span>90 Minutes</span></div>
  <h3>MYOFASCIAL RELEASE</h3>
</div>
<div class="abs rate" style="left:780px;top:1354px">
  <div class="ring">$ 120<span>120 Minutes</span></div>
  <h3>SPONTANEOUS MUSCLE RELEASE</h3>
</div>

<!-- info columns -->
<h3 class="abs col-title" style="left:99px;top:1596px">Massage Therapy</h3>
<div class="abs therapy-card" role="img" aria-label="Photo of a client relaxing on a massage table with towels and candles">
  <h4>MEDICAL MASSAGE.</h4>
  <div class="stars">
    <svg width="90" height="16" viewBox="0 0 90 16" aria-hidden="true"><g fill="#f2c21b"><path id="st" d="M8 0l2.4 5 5.4.6-4 3.7 1.1 5.4L8 12l-4.9 2.7 1.1-5.4-4-3.7 5.4-.6z"/><use href="#st" x="18"/><use href="#st" x="37"/><use href="#st" x="55"/><use href="#st" x="74"/></g></svg>
  </div>
  <p>We specialize in integrated Pain management, and sports/medical massage therapy.</p>
  <span class="more">READ MORE &gt;&gt;</span>
</div>

<h3 class="abs col-title" style="left:477px;top:1601px">Our Passion</h3>
<p class="abs col-text" style="left:477px;top:1628px;width:300px">Here at Kestrel Way, we have a great passion for Postural Resoration and how it is&nbsp; integrated into an individual's Massage treatment.</p>
<ul class="abs passion-list" style="left:477px;top:1700px">
  <li><svg width="11" height="11" viewBox="0 0 11 11" aria-hidden="true"><circle cx="5.5" cy="5.5" r="4.6" fill="none" stroke="#1f78b8" stroke-width="1.4"/><path d="M4.5 3.3l2.2 2.2-2.2 2.2" fill="none" stroke="#1f78b8" stroke-width="1.4"/></svg>Neuromuscular</li>
  <li><svg width="11" height="11" viewBox="0 0 11 11" aria-hidden="true"><circle cx="5.5" cy="5.5" r="4.6" fill="none" stroke="#1f78b8" stroke-width="1.4"/><path d="M4.5 3.3l2.2 2.2-2.2 2.2" fill="none" stroke="#1f78b8" stroke-width="1.4"/></svg>Myofascial release</li>
  <li><svg width="11" height="11" viewBox="0 0 11 11" aria-hidden="true"><circle cx="5.5" cy="5.5" r="4.6" fill="none" stroke="#1f78b8" stroke-width="1.4"/><path d="M4.5 3.3l2.2 2.2-2.2 2.2" fill="none" stroke="#1f78b8" stroke-width="1.4"/></svg>Spontaneous muscle release</li>
  <li><svg width="11" height="11" viewBox="0 0 11 11" aria-hidden="true"><circle cx="5.5" cy="5.5" r="4.6" fill="none" stroke="#1f78b8" stroke-width="1.4"/><path d="M4.5 3.3l2.2 2.2-2.2 2.2" fill="none" stroke="#1f78b8" stroke-width="1.4"/></svg>Postural restoration</li>
  <li><svg width="11" height="11" viewBox="0 0 11 11" aria-hidden="true"><circle cx="5.5" cy="5.5" r="4.6" fill="none" stroke="#1f78b8" stroke-width="1.4"/><path d="M4.5 3.3l2.2 2.2-2.2 2.2" fill="none" stroke="#1f78b8" stroke-width="1.4"/></svg>Orthopedic</li>
  <li><svg width="11" height="11" viewBox="0 0 11 11" aria-hidden="true"><circle cx="5.5" cy="5.5" r="4.6" fill="none" stroke="#1f78b8" stroke-width="1.4"/><path d="M4.5 3.3l2.2 2.2-2.2 2.2" fill="none" stroke="#1f78b8" stroke-width="1.4"/></svg>Medical massage.</li>
</ul>

<h3 class="abs col-title" style="left:801px;top:1601px">Our education</h3>
<p class="abs col-text edu-text" style="left:801px;top:1627px;width:290px">We are both Graduates of Venmora, school of massage therapy. We have continuing&nbsp; education in medical massage, myofacial release, trigger point therapy, postural restoration, anatomy, and spontaneous muscle release. Lina is also a Certified Yoga&nbsp; Instructor, which amplifies her experience with flexibility and strength as it pertains to each individual.</p>
<a class="abs read-more" style="left:806px;top:1834px;margin:0">READ MORE &gt;&gt;</a>

<!-- testimonials -->
<section class="abs testimonials">
  <h3>TESTIMONIALS</h3>
  <blockquote>The most important thing to 'us', as Licenced providers is to get you on to our table to show you our skills. But a good therapist never forgets that it's not about what we do for you, but what we can facilitate for you. Your health and healing has nothing to do with us.
    <cite>- DANA WHITFIELD</cite>
  </blockquote>
</section>
<div class="abs brand-badge small-logo">Kestrel<br>Way</div>
<svg class="abs arrow" style="left:130px" width="14" height="24" viewBox="0 0 14 24" aria-hidden="true"><path d="M12 2L3 12l9 10" fill="none" stroke="#b5b5b5" stroke-width="2"/></svg>
<svg class="abs arrow" style="left:1052px" width="14" height="24" viewBox="0 0 14 24" aria-hidden="true"><path d="M2 2l9 10-9 10" fill="none" stroke="#b5b5b5" stroke-width="2"/></svg>

<!-- footer -->
<footer class="abs footer"></footer>
<div class="abs brand-badge footer-logo">Kestrel<br>Way</div>

<h4 class="abs foot-title" style="left:348px;top:2120px">Our passions</h4>
<ul class="abs foot-list" style="left:350px;top:2150px">
  <li>Neuromuscular</li>
  <li>Myofascial release</li>
  <li>Spontaneous muscle release,</li>
  <li>Postural restoration,</li>
  <li>Orthopedic,</li>
  <li>Medical massage.</li>
</ul>

<h4 class="abs foot-title" style="left:609px;top:2120px">Latest Tweets</h4>
<div class="abs tweet-box">
  <svg width="14" height="14" viewBox="0 0 14 14" aria-hidden="true" style="float:left;margin:3px 10px 0 18px"><circle cx="7" cy="7" r="6" fill="#3aa3e3"/></svg>
  Check out&nbsp; - Responsive PressLeaf Blogging Theme' on #Lorem Ipsum edenchase @Osteopathy
  <span class="summary">show Summary</span>
</div>

<h4 class="abs foot-title" style="left:892px;top:2120px">Contact Us</h4>
<div class="abs contact-item" style="top:2160px">
  <svg width="11" height="14" viewBox="0 0 11 14" aria-hidden="true"><path d="M5.5 0C2.5 0 0 2.3 0 5.3 0 9 5.5 14 5.5 14S11 9 11 5.3C11 2.3 8.5 0 5.5 0z" fill="#fff"/><circle cx="5.5" cy="5.2" r="2" fill="#333"/></svg>
  <span>410 Alder Street, Seattle,<br>WA 98101</span>
</div>
<div class="abs contact-item" style="top:2199px">
  <svg width="12" height="12" viewBox="0 0 12 12" aria-hidden="true"><path d="M2.2 0l2.2 3-1.3 1.5c.8 1.8 2 3 3.8 3.8L8.4 7 11.6 9l-.9 2.6C5 12 0 7 .3 1.2z" fill="#fff"/></svg>
  <span>(206) 555-0148</span>
</div>
<div class="abs contact-item" style="top:2228px">
  <svg width="12" height="14" viewBox="0 0 12 14" aria-hidden="true"><rect x="2" y="0" width="8" height="14" rx="1.5" fill="#fff"/><rect x="3.4" y="1.8" width="5.2" height="8.6" fill="#333"/></svg>
  <span>(206) 555-0148</span>
</div>
<div class="abs contact-item" style="top:2258px">
  <svg width="14" height="11" viewBox="0 0 14 11" aria-hidden="true"><rect width="14" height="11" rx="1" fill="#fff"/><path d="M1 1.5l6 4.5 6-4.5" fill="none" stroke="#333" stroke-width="1.3"/></svg>
  <span style="text-decoration:underline">kestrelwaymassage@fernmail.net</span>
</div>

<div class="abs foot-rule"></div>
<p class="abs copyright">Copyright © 2015, Kestrel Way | All Rights Reserved.</p>

</body>
</html>
```